Brell Stone Company Business Cards

Front and Back Business Card - logo and text setup - cool design. I need workable photoshop or illustrator files so I can setup each employee card with design that is created
Updates

Hi everyone, thank you for the great entries. Please no more white and blue cards - there are so many already - black and silver only now please. thanks!

Target Market(s)

Construction Industry - Facility Managers

Industry/Entity Type

Construction

Contact Information for Business Card

I really like contemporary simplistic looks - clean neat....not opposed to seeing some black backrounds

Requirements
Must have
• Logo/website address with design on front only - www.brellstone-example.com (logo attached)
• Back:
• Name/Title/Company Address/Phone/email address
Nice to have
• Cool design
Should not have
• Nothing gimmicky like Fire or Water - since we are a Fire Protection company - it has all been done

```html
<!DOCTYPE html>
<html lang="en">
<head>
<meta charset="utf-8">
<title>Brell Stone Company – Business Cards</title>
<link rel="stylesheet" href="https://fonts.googleapis.com/css2?family=PT+Sans:wght@400;700&display=swap">
<style>
  :root {
    --backdrop-center: #e8e9ea;
    --backdrop-edge: #cdced0;
    --silver-light: #f1f2f3;
    --silver-mid: #d6d7d9;
    --silver-deep: #a7a9ac;
    --card-dark: #262425;
    --card-dark-soft: #3d3b3d;
    --ink: #231f20;
    --ink-muted: #4a4647;
    --on-dark: #e9eaeb;
    --on-dark-muted: #c4c6c8;
  }
  * { box-sizing: border-box; margin: 0; padding: 0; }
  html, body { width: 800px; height: 1200px; overflow: hidden; }
  body {
    position: relative;
    font-family: "PT Sans", sans-serif;
    background: radial-gradient(ellipse at 50% 50%, var(--backdrop-center) 0%, var(--backdrop-edge) 75%);
  }
  .card {
    position: absolute;
    width: 502px;
    height: 288px;
    overflow: hidden;
  }

  /* Front */
  .card-front {
    left: 149px;
    top: 174px;
    background: linear-gradient(160deg, var(--silver-light) 0%, var(--silver-mid) 70%, var(--silver-deep) 100%);
  }
  .card-front .wave { position: absolute; inset: 0; width: 100%; height: 100%; }
  .brand-name {
    position: absolute;
    left: 18px;
    top: 26px;
    display: flex;
    align-items: center;
    gap: 10px;
    font-weight: 700;
    font-size: 40px;
    line-height: 1;
    color: var(--ink);
  }
  .brand-mark { width: 14px; height: 14px; background: var(--silver-deep); }
  .holder { position: absolute; left: 21px; top: 176px; color: var(--ink); }
  .holder-name { font-size: 22px; font-weight: 700; line-height: 1.1; }
  .holder-title { font-size: 13px; color: var(--ink-muted); line-height: 1.2; }
  .contact-list {
    position: absolute;
    right: 14px;
    top: 182px;
    list-style: none;
    color: var(--on-dark);
    font-size: 13px;
    text-align: right;
  }
  .contact-list li {
    display: flex;
    justify-content: flex-end;
    align-items: center;
    gap: 8px;
    height: 20px;
    margin-bottom: 16px;
  }
  .contact-list svg { width: 10px; height: 12px; fill: var(--on-dark); }

  /* Back */
  .card-back {
    left: 148px;
    top: 704px;
    width: 504px;
    height: 287px;
    background: radial-gradient(ellipse at 50% 35%, var(--card-dark-soft) 0%, var(--card-dark) 60%);
    color: var(--on-dark);
    text-align: center;
  }
  .card-back .brand-name {
    position: static;
    justify-content: center;
    margin-top: 112px;
    font-size: 44px;
    color: var(--on-dark);
  }
  .website { margin-top: 40px; font-size: 13px; color: var(--on-dark-muted); }
</style>
</head>
<body>

<section class="card card-front" aria-label="Business card front">
  <svg class="wave" viewBox="0 0 502 288" preserveAspectRatio="none" aria-hidden="true">
    <defs>
      <linearGradient id="darkFill" x1="0" y1="0" x2="1" y2="0">
        <stop offset="0" stop-color="#3d3b3d"/>
        <stop offset="0.5" stop-color="#2a2829"/>
        <stop offset="1" stop-color="#1f1d1e"/>
      </linearGradient>
    </defs>
    <path d="M0,228 C120,258 300,236 502,64 L502,76 C300,246 120,262 0,234 Z" fill="#231f20"/>
    <path d="M0,233 C130,272 310,248 502,90 L502,288 L0,288 Z" fill="url(#darkFill)"/>
  </svg>

  <div class="brand-name"><span>Brell Stone</span><span class="brand-mark"></span></div>

  <div class="holder">
    <p class="holder-name">Daniel Harwick</p>
    <p class="holder-title">Managing Member</p>
  </div>

  <ul class="contact-list">
    <li>0300-555-014
      <svg viewBox="0 0 10 12" aria-hidden="true"><path d="M2,1 L4,1 L5,4 L3.6,5 C4.3,6.6 5.2,7.6 6.6,8.3 L7.6,7 L10,8.2 L9.6,10.4 C5,11 1,6.5 1.2,2 Z"/></svg>
    </li>
    <li>@yourweb.com
      <svg viewBox="0 0 10 12" aria-hidden="true"><path d="M0,3 L10,3 L10,10 L0,10 Z M0.8,3.6 L5,7 L9.2,3.6 Z" fill-rule="evenodd"/></svg>
    </li>
    <li>your address here
      <svg viewBox="0 0 10 12" aria-hidden="true"><path d="M5,0 C2.3,0 0.6,2 0.6,4.3 C0.6,7.3 5,12 5,12 C5,12 9.4,7.3 9.4,4.3 C9.4,2 7.7,0 5,0 Z M5,2.6 A1.7,1.7 0 1 0 5,6 A1.7,1.7 0 1 0 5,2.6 Z" fill-rule="evenodd"/></svg>
    </li>
  </ul>
</section>

<section class="card card-back" aria-label="Business card back">
  <div class="brand-name"><span>Brell Stone</span><span class="brand-mark"></span></div>
  <p class="website">www.brellstone-example.com</p>
</section>

</body>
</html>
```